BorrowNest Website design, we are a home loan / lending company

We are a finance broking company that can do mortgages / home loans, Car Loans, Commercial Loans, SMSF Loans, Business Loans, Personal Loans
We are looking for a simple website, not too busy, easy to navigate, something that prompts customers to action or call us.
I like the simplicity of the following websites:
https://www.velkarafinance.com.au/ - I like this website front page. I was thinking I have my logo, the one with the black background appear , then the toolbar at the top perhaps?
https://trevix.com.au/business-loans# - on this page there are images under finance that works for you that I like that concept.
https://dunmerel.com.au/contact/ - I like the Make an Appointment page
https://trevix.com.au/about-us - Simple but effective page design

Target Market(s)

Home Loan Customer

Industry/Entity Type

Finance / Home Loans

Coding

Coded - Design and coding required

Number of Pages Required

5+ page

Font styles to use
Serif

Colors
0094D4
00A9DD
6FCCEA
C7EBF8
E9F6FB

Requirements
Must have
• The following Heading s - Contact Us, About Us, Our People, Make an Appointment, Loan Options, Calculators, Reviews. I want to use the Logo colours I have in the zip files I uploaded.
Nice to have
• Simple clean design

```html
<!DOCTYPE html>
<html lang="en">
<head>
<meta charset="utf-8">
<title>BorrowNest – Finance Broking</title>
<link href="https://fonts.googleapis.com/css2?family=Montserrat:wght@500;600;700&family=Roboto:wght@400;500;700&display=swap" rel="stylesheet">
<style>
:root{
  --cyan:#00c4f0;
  --cyan-dark:#00a9dd;
  --blue:#0094d4;
  --ink:#222428;
  --body:#6b6f75;
  --light:#f3f4f6;
  --line:#c9ccd1;
  --footer:#17191c;
  --white:#ffffff;
  --frame:#eef0f2;
}
*{box-sizing:border-box;margin:0;padding:0}
html,body{width:1200px;height:4181px;overflow:hidden}
body{position:relative;font-family:'Roboto',sans-serif;color:var(--body);background:var(--white)}
.abs{position:absolute}
.head-font{font-family:'Montserrat',sans-serif}
.accent{color:var(--blue)}
.btn{position:absolute;display:flex;align-items:center;justify-content:center;gap:6px;background:var(--cyan);color:var(--white);font:700 13px 'Roboto',sans-serif;border-radius:24px;box-shadow:0 4px 10px rgba(0,160,220,.35);text-transform:uppercase}
.btn .dot{width:12px;height:12px;border-radius:50%;background:var(--white);position:relative}
.btn .dot::after{content:"";position:absolute;left:3px;top:3px;border-left:6px solid var(--cyan);border-top:3px solid transparent;border-bottom:3px solid transparent}
.para{font-size:13.5px;line-height:26px}

/* header */
.topbar{left:0;top:0;width:1200px;height:78px;background:var(--cyan)}
.brand{font-family:'Montserrat',sans-serif;font-weight:600;color:var(--white)}
.topbar .brand{left:110px;top:18px;font-size:34px}
.topbar .meta{top:28px;font-size:12px;color:var(--white);display:flex;align-items:center;gap:6px}
.flag{width:22px;height:22px;border-radius:50%;background:#d9dde6;border:2px solid var(--white)}
.call-circle{left:860px;top:16px;width:46px;height:46px;border-radius:50%;background:var(--white);display:flex;align-items:center;justify-content:center}
.call-label{left:916px;top:18px;color:var(--white);font-size:12px;font-weight:500}
.call-num{left:916px;top:34px;color:var(--white);font:600 21px 'Montserrat',sans-serif}
.nav{left:0;top:78px;width:1200px;height:55px;background:var(--cyan-dark)}
.nav ul{list-style:none;display:flex;position:absolute;left:101px;top:0;height:55px}
.nav li{height:55px;display:flex;align-items:center;padding:0 14px;color:var(--white);font:600 13px 'Montserrat',sans-serif;text-transform:uppercase}
.nav li.active{background:var(--blue)}

/* hero */
.hero{left:0;top:133px;width:1200px;height:627px;background:linear-gradient(100deg,#b8c3c9 0%,#9fadb5 25%,#7c8f9c 55%,#5f7686 100%)}
.hero-brand{left:630px;top:378px;font-size:64px}
.hero-tag{left:634px;top:462px;font:500 21px 'Montserrat',sans-serif;color:var(--white)}
.scroll{left:572px;top:732px;width:56px;height:56px;border-radius:50%;background:var(--white);display:flex;justify-content:center;padding-top:14px}
.scroll-label{left:0;top:784px;width:1200px;text-align:center;font-size:13px;color:var(--ink);letter-spacing:.3px}

/* about */
.about-backdrop{left:106px;top:848px;width:200px;height:526px;background:var(--frame);border-radius:4px}
.about-photo{left:143px;top:882px;width:424px;height:448px;border-radius:26px;background:linear-gradient(135deg,#cfd6d4,#8c9997 55%,#4b5655)}
.pill{position:absolute;background:var(--cyan);color:var(--white);font:700 12px 'Roboto',sans-serif;border-radius:16px;text-transform:uppercase;display:flex;align-items:center;justify-content:center}
.about-title{left:598px;top:942px;font:600 53px 'Montserrat',sans-serif;color:var(--ink)}
.about-text{left:598px;top:1015px;width:492px;text-align:justify}

/* services */
.services{left:0;top:1418px;width:1200px;height:625px;background:linear-gradient(90deg,#f3f4f5,#eceeef 70%,#e4e6e7)}
.sec-title{left:0;width:1200px;text-align:center;font:600 47px 'Montserrat',sans-serif;color:var(--ink)}
.card{position:absolute;top:1570px;width:313px;height:383px;background:var(--white);border-radius:8px;box-shadow:0 2px 10px rgba(0,0,0,.08)}
.card .pic{position:absolute;left:9px;top:9px;width:295px;height:178px}
.card h3{position:absolute;left:22px;top:205px;font:500 18px 'Roboto',sans-serif;color:var(--ink)}
.card p{position:absolute;left:23px;top:238px;width:270px;font-size:13.5px;line-height:26px}
.round{position:absolute;left:24px;top:328px;width:38px;height:38px;border-radius:50%;background:#e8e9eb;display:flex;align-items:center;justify-content:center}
.chev{top:1746px}

/* steps */
.step{position:absolute;top:2213px;width:300px;text-align:center}
.step .circle{margin:0 auto;width:126px;height:126px;border-radius:50%;background:#e6e7e9;position:relative;display:flex;align-items:center;justify-content:center}
.step .num{position:absolute;left:43px;top:-22px;width:40px;height:40px;border-radius:50%;background:var(--cyan);border:4px solid var(--white);color:var(--white);font:700 12px 'Roboto',sans-serif;display:flex;align-items:center;justify-content:center}
.step h4{margin-top:22px;font:600 22px 'Montserrat',sans-serif;color:var(--ink)}
.step p{margin-top:8px;font-size:13.5px;line-height:26px;padding:0 10px}

/* people */
.people{left:0;top:2561px;width:1200px;height:534px;background:linear-gradient(100deg,#9c8f84,#6f6a68 40%,#3e4148 70%,#2a2e36)}
.people-box{left:117px;top:2671px;width:550px;height:314px;background:rgba(30,30,34,.72)}
.people-box h2{position:absolute;left:25px;top:18px;font:600 53px 'Montserrat',sans-serif;color:var(--white)}
.people-box p{position:absolute;left:29px;top:96px;width:491px;color:#e8e8e8;text-align:justify}

/* appointment */
.appt-bg{left:0;top:3112px;width:1200px;height:597px;background:linear-gradient(180deg,#ffffff 0%,#f6f7f8 55%,#eeeff1 100%)}
.field{position:absolute;background:var(--white);border:1px solid var(--line);border-radius:3px;font-size:13.5px;color:#777;padding:0 18px;display:flex;align-items:center}

/* footer */
.footer{left:0;top:3709px;width:1200px;height:472px;background:var(--footer)}
.footer-brand{left:0;width:1200px;text-align:center;top:3766px;font-size:36px}
.fcol{position:absolute;top:3863px}
.fcol h5{font:500 21px 'Roboto',sans-serif;color:var(--white)}
.fcol h5::after{content:"";display:block;width:28px;height:3px;background:var(--cyan);margin-top:10px}
.fcol ul{list-style:none;margin-top:20px}
.fcol li{height:26px;font-size:13.5px;color:#e6e6e6;display:flex;align-items:center;gap:12px}
.fcol li .mk{width:8px;color:var(--cyan);font-size:12px}
.fcol li .sq{width:10px;height:10px;border-radius:2px;background:var(--cyan)}
.copy{left:0;top:4108px;width:1200px;border-top:1px solid #33363a;padding-top:12px;text-align:center;font-size:13.5px;color:#e6e6e6}
</style>
</head>
<body>

<!-- Header -->
<header>
  <div class="abs topbar">
    <div class="abs brand">BorrowNest</div>
    <div class="abs meta" style="left:686px"><span>Eng</span><span class="flag"></span></div>
    <div class="abs meta" style="left:780px">
      <svg width="10" height="12" viewBox="0 0 10 12"><rect x="1" y="5" width="8" height="7" rx="1" fill="#fff"/><path d="M3 5V3.5a2 2 0 0 1 4 0V5" stroke="#fff" stroke-width="1.5" fill="none"/></svg>
      <span>Log In</span>
    </div>
    <div class="abs call-circle">
      <svg width="20" height="20" viewBox="0 0 24 24"><path d="M6.6 10.8a15 15 0 0 0 6.6 6.6l2.2-2.2a1 1 0 0 1 1-.25 11 11 0 0 0 3.6.6 1 1 0 0 1 1 1V20a1 1 0 0 1-1 1A17 17 0 0 1 3 4a1 1 0 0 1 1-1h3.5a1 1 0 0 1 1 1c0 1.25.2 2.45.6 3.6a1 1 0 0 1-.25 1z" fill="#00c4f0"/></svg>
    </div>
    <div class="abs call-label">Call us Today :</div>
    <div class="abs call-num">+1 888 888 8888</div>
  </div>
  <nav class="abs nav">
    <ul>
      <li class="active">Home</li><li>Contact Us</li><li>About Us</li><li>Our People</li><li>Loan Options</li><li>Make an Appointment</li><li>Calculators</li><li>Reviews</li>
    </ul>
  </nav>
</header>

<!-- Hero -->
<section>
  <div class="abs hero" role="img" aria-label="Photo of a hand holding a small orange model house beside stacks of coins"></div>
  <div class="abs brand hero-brand">BorrowNest</div>
  <div class="abs hero-tag">We are a finance broking company</div>
  <div class="btn" style="left:634px;top:507px;width:160px;height:45px">Get Started <span class="dot"></span></div>
  <div class="abs scroll">
    <svg width="18" height="20" viewBox="0 0 18 20"><path d="M9 2v14M3 10l6 6 6-6" stroke="#222" stroke-width="2.6" fill="none"/></svg>
  </div>
  <div class="abs scroll-label">SCROLL DOWN</div>
</section>

<!-- About -->
<section>
  <div class="abs about-backdrop" role="img" aria-label="Decorative backdrop framing the about photo"></div>
  <div class="abs about-photo" role="img" aria-label="Photo of two colleagues reviewing documents on a clipboard in an office"></div>
  <div class="pill" style="left:600px;top:897px;width:113px;height:33px">About Us</div>
  <div class="abs about-title">BorrowNest</div>
  <div class="abs about-text para">
    <p>Lorem ipsum dolor sit amet, consectetur adipiscing elit, sed do eiusmod tempor incididunt ut labore et dolore magna aliqua. Ut enim ad minim venia m, quis nostrud exercitation ullamco laboris nisi ut aliquip ex ea commodo consequat. Duis aute irure dolor in reprehenderit in voluptate velit esse cillu m dolore eu fugiat nulla pariatur.</p>
    <p style="margin-top:25px">Excepteur sint occaecat cupidatat non proi dent, sunt in culpa qui officia deserunt mollit anim id est laborum. Duis aute irure dolor in reprehenderit in voluptate velit esse cillu m dolore eu fugiat nulla pariatur.</p>
  </div>
  <div class="btn" style="left:600px;top:1275px;width:160px;height:45px">Learn More <span class="dot"></span></div>
</section>

<!-- Services -->
<section>
  <div class="abs services" role="img" aria-label="Faint photo of keys being handed over across a desk"></div>
  <h2 class="abs sec-title" style="top:1490px">Our <span class="accent">Services</span></h2>
  <svg class="abs chev" style="left:48px" width="14" height="22" viewBox="0 0 14 22"><path d="M11 2L3 11l8 9" stroke="#222" stroke-width="2.5" fill="none"/></svg>
  <svg class="abs chev" style="left:1137px" width="14" height="22" viewBox="0 0 14 22"><path d="M3 2l8 9-8 9" stroke="#222" stroke-width="2.5" fill="none"/></svg>

  <article class="card" style="left:110px">
    <div class="pic" role="img" aria-label="Photo of a calculator and small model houses on a desk" style="background:linear-gradient(135deg,#8d969a,#4a5256)"></div>
    <h3>Home Loans</h3>
    <p>Lorem ipsum dolor sit amet, consectetur adipiscing elit, sed do eiusmod tempor incididunt ut labore et dolore</p>
    <div class="round"><svg width="12" height="12" viewBox="0 0 12 12"><path d="M1 6h9M6 2l4 4-4 4" stroke="#222" stroke-width="2" fill="none"/></svg></div>
  </article>
  <article class="card" style="left:445px;height:391px">
    <div class="pic" role="img" aria-label="Photo of car keys handed over a signed contract" style="background:linear-gradient(135deg,#d9dcdd,#a8aeb1)"></div>
    <h3>Car Loans</h3>
    <p>Lorem ipsum dolor sit amet, consectetur adipiscing elit, sed do eiusmod tempor incididunt ut labore et dolore</p>
    <div class="btn" style="left:24px;top:325px;width:160px;height:44px">Learn More <span class="dot"></span></div>
  </article>
  <article class="card" style="left:776px">
    <div class="pic" role="img" aria-label="Photo of a business document being stamped at a meeting table" style="background:linear-gradient(135deg,#b9b2a6,#6f6a62)"></div>
    <h3>Commercial Loans</h3>
    <p>Lorem ipsum dolor sit amet, consectetur adipiscing elit, sed do eiusmod tempor incididunt ut labore et dolore</p>
    <div class="round"><svg width="12" height="12" viewBox="0 0 12 12"><path d="M1 6h9M6 2l4 4-4 4" stroke="#222" stroke-width="2" fill="none"/></svg></div>
  </article>
</section>

<!-- Steps -->
<section>
  <h2 class="abs sec-title" style="top:2120px">Easy to apply. <span class="accent">Simple as 1, 2, 3.</span></h2>
  <div class="step" style="left:125px">
    <div class="circle"><span class="num">01</span>
      <svg width="56" height="56" viewBox="0 0 56 56" fill="none" stroke="#222" stroke-width="2.4"><path d="M42 8c-10 0-20 6-26 18l10 10c12-6 18-16 18-26z"/><circle cx="33" cy="21" r="4"/><path d="M16 26l-7 1 5 5M26 36l-1 7-5-5M14 40l-6 6"/></svg>
    </div>
    <h4>Get started</h4>
    <p>Lorem ipsum dolor sit amet, consectetur adipiscing elit, sed do eiusmod tempor incididunt</p>
  </div>
  <div class="step" style="left:451px">
    <div class="circle"><span class="num">02</span>
      <svg width="60" height="60" viewBox="0 0 60 60" fill="none" stroke="#222" stroke-width="2.4"><rect x="8" y="26" width="28" height="14" rx="7" transform="rotate(-45 22 33)"/><rect x="24" y="20" width="28" height="14" rx="7" transform="rotate(-45 38 27)"/></svg>
    </div>
    <h4>Link your data</h4>
    <p>Lorem ipsum dolor sit amet, consectetur adipiscing elit, sed do eiusmod tempor incididunt</p>
  </div>
  <div class="step" style="left:776px">
    <div class="circle"><span class="num">03</span>
      <svg width="60" height="60" viewBox="0 0 60 60" fill="none" stroke="#222" stroke-width="2.4"><circle cx="36" cy="20" r="11"/><path d="M36 13v14M39 16h-4a2 2 0 0 0 0 4h2a2 2 0 0 1 0 4h-4"/><path d="M6 42h10l8 3h10a2 2 0 0 0 0-4h-8M16 50h22l14-10a3 3 0 0 0-4-4l-8 5M6 38v16"/></svg>
    </div>
    <h4>Get funds fast</h4>
    <p>Lorem ipsum dolor sit amet, consectetur adipiscing elit, sed do eiusmod tempor incididunt</p>
  </div>
</section>

<!-- People -->
<section>
  <div class="abs people" role="img" aria-label="Photo of a broker meeting with clients at an office desk"></div>
  <div class="abs people-box">
    <h2>Our People</h2>
    <p class="para">Lorem ipsum dolor sit amet, consectetur adipiscing elit, sed do eiusmod tempor incididunt ut labore et dolore magna aliqua. Ut enim ad minim venia m, quis nostrud exercitation ullamco laboris nisi ut aliquip ex ea commodo consequat. Duis aute irure dolor in reprehenderit in voluptate velit esse cillu m dolore eu fugiat nulla pariatur.</p>
    <div class="btn" style="left:31px;top:241px;width:160px;height:44px">Learn More <span class="dot"></span></div>
  </div>
</section>

<!-- Appointment -->
<section>
  <div class="abs appt-bg" role="img" aria-label="Faint photo of a laptop on a desk"></div>
  <h2 class="abs sec-title" style="top:3172px">Make <span class="accent">an Appointment</span></h2>
  <p class="abs" style="left:0;top:3240px;width:1200px;text-align:center;font-size:13.5px">Lorem ipsum dolor sit amet, consectetur adipiscing elit, sed do eiusmod tempor incididunt</p>
  <div class="field" style="left:196px;top:3287px;width:396px;height:55px">Name</div>
  <div class="field" style="left:607px;top:3287px;width:396px;height:55px">Email address</div>
  <div class="field" style="left:196px;top:3362px;width:807px;height:54px">Phone</div>
  <div class="field" style="left:196px;top:3438px;width:807px;height:123px;align-items:flex-start;padding-top:18px">Message</div>
  <div class="btn" style="left:520px;top:3578px;width:160px;height:44px">Submit Now</div>
</section>

<!-- Footer -->
<footer>
  <div class="abs footer" role="img" aria-label="Dark faded photo of city buildings"></div>
  <div class="abs brand footer-brand">BorrowNest</div>

  <div class="fcol" style="left:109px">
    <h5>Quick links</h5>
    <ul><li><span class="mk">›</span>Home</li><li><span class="mk">›</span>Contact Us</li><li><span class="mk">›</span>About Us</li><li><span class="mk">›</span>Our People</li><li><span class="mk">›</span>Make an Appointment</li><li><span class="mk">›</span>Loan Options</li></ul>
  </div>
  <div class="fcol" style="left:367px">
    <h5>Information</h5>
    <ul><li><span class="mk">›</span>Calculators</li><li><span class="mk">›</span>Reviews</li><li><span class="mk">›</span>Privacy policy</li><li><span class="mk">›</span>Terms &amp; Condition</li><li><span class="mk">›</span>Support</li><li><span class="mk">›</span>Faq</li></ul>
  </div>
  <div class="fcol" style="left:607px">
    <h5>Follow us</h5>
    <ul><li><span class="sq"></span>Pagefold</li><li><span class="sq"></span>Chirpline</li><li><span class="sq"></span>Snapframe</li><li><span class="sq"></span>Streamtube</li><li><span class="sq"></span>Workring</li><li><span class="sq"></span>Orbitplus</li></ul>
  </div>
  <div class="fcol" style="left:845px">
    <h5>Contact us</h5>
    <ul>
      <li style="height:52px;align-items:flex-start;gap:22px"><svg width="10" height="14" viewBox="0 0 10 14" style="margin-top:6px"><path d="M5 0a5 5 0 0 1 5 5c0 4-5 9-5 9S0 9 0 5a5 5 0 0 1 5-5z" fill="#00c4f0"/><circle cx="5" cy="5" r="2" fill="#17191c"/></svg><span style="line-height:26px">Lorem ipsum dolor sit amet, con<br>ut labore et dolore</span></li>
      <li style="gap:22px"><svg width="12" height="12" viewBox="0 0 24 24"><path d="M6.6 10.8a15 15 0 0 0 6.6 6.6l2.2-2.2a1 1 0 0 1 1-.25 11 11 0 0 0 3.6.6 1 1 0 0 1 1 1V20a1 1 0 0 1-1 1A17 17 0 0 1 3 4a1 1 0 0 1 1-1h3.5a1 1 0 0 1 1 1c0 1.25.2 2.45.6 3.6a1 1 0 0 1-.25 1z" fill="#00c4f0"/></svg>+1 888 888 8888</li>
      <li style="gap:20px;margin-top:26px"><svg width="14" height="10" viewBox="0 0 14 10"><rect width="14" height="10" rx="1" fill="#00c4f0"/><path d="M0 1l7 5 7-5" stroke="#17191c" stroke-width="1.3" fill="none"/></svg>info@companyname.com</li>
    </ul>
  </div>

  <div class="abs copy">© Copyright 2022 Company name | All Rights Reserved</div>
</footer>

</body>
</html>
```